Business cards and stationary design

We just completed the design of our new logo and we need to print new business cards and letterhead for our nonprofit. We are looking for a fresh new design that shows off our new logo. On letterhead, we must have a column on the right or left to include our Board of Directors (up to 45 names) (see attachment)

Industry/Entity Type

Non-Profit

Contact Information for Business Card

Standard business card with name, title, Company name, mailing address phone numbers, email address and website. Tagline on back "Opening Doors To Shelter"

Font styles to use
Sans Serif

Requirements
Must have
• include pertinent information above
• new logo
• fonts compatible with logo
• should use logo colors only
Nice to have
• tag lines

```html
<!DOCTYPE html>
<html lang="en">
<head>
<meta charset="utf-8">
<title>Hearthway Housing Center – Business Card</title>
<link rel="stylesheet" href="https://fonts.googleapis.com/css2?family=Open+Sans:wght@400;600&display=swap">
<style>
  :root {
    --teal: #2a7b8e;
    --red: #d33a36;
    --ink: #3e3e3e;
    --paper: #f7f7f5;
    --backdrop: #8e8e8c;
    --photo-light: #b9b9b9;
    --photo-dark: #3a3a3a;
  }
  * { box-sizing: border-box; margin: 0; padding: 0; }
  html, body { width: 1200px; height: 1000px; overflow: hidden; }
  body {
    background: var(--backdrop);
    font-family: "Open Sans", sans-serif;
    color: var(--ink);
    position: relative;
  }
  .card {
    position: absolute;
    left: 250px;
    width: 700px;
    height: 400px;
    background: var(--paper);
    overflow: hidden;
    box-shadow: 0 6px 18px rgba(0,0,0,.25);
  }
  .card--back { top: 60px; }
  .card--front { top: 540px; }

  /* Back side */
  .back-photo {
    position: absolute; inset: 0;
    background: linear-gradient(160deg, var(--photo-dark) 0%, #6b6b6b 35%, var(--photo-light) 70%, #8a8a8a 100%);
  }
  .back-banner {
    position: absolute;
    left: 40px; top: 40px;
    width: 360px; height: 92px;
    background: rgba(42,123,142,.88);
    padding: 16px 22px;
    color: #fff;
  }
  .back-banner .org-name {
    font-size: 22px; font-weight: 600; letter-spacing: 1.5px; text-transform: uppercase;
    display: flex; align-items: center; gap: 10px; white-space: nowrap;
  }
  .back-banner .org-dot { width: 12px; height: 12px; border-radius: 50%; background: #fff; flex: none; }
  .back-banner .tagline { margin-top: 8px; font-size: 17px; letter-spacing: .3px; white-space: nowrap; }

  /* Front side */
  .front-logo {
    position: absolute; top: 70px; left: 0; right: 0;
    display: flex; justify-content: center; align-items: center; gap: 12px;
  }
  .front-logo .org-dot { width: 16px; height: 16px; border-radius: 50%; background: var(--red); }
  .front-logo .org-name {
    font-size: 25px; font-weight: 600; letter-spacing: 2px; color: var(--teal); text-transform: uppercase;
  }
  .logo-rule {
    position: absolute; top: 118px; left: 200px; width: 300px; height: 1px; background: var(--red);
  }
  .rule { position: absolute; height: 2px; background: var(--teal); }
  .rule--upper { top: 165px; left: 50px; width: 330px; }
  .rule--lower { top: 262px; left: 340px; width: 310px; }

  .person { position: absolute; top: 172px; left: 0; right: 0; text-align: center; }
  .person .name { font-size: 21px; font-weight: 600; color: var(--teal); letter-spacing: .5px; }
  .person .title { font-size: 14px; color: #222; }

  .address {
    position: absolute; top: 200px; left: 55px;
    font-size: 18px; line-height: 1.3; color: var(--ink);
  }
  .address span { display: block; padding-left: 20px; }

  .contacts {
    position: absolute; top: 280px; left: 380px;
    list-style: none; font-size: 15px; color: #222;
  }
  .contacts li { display: flex; align-items: center; gap: 12px; height: 30px; }
  .contacts .icon {
    width: 20px; height: 20px; border-radius: 50%; background: var(--teal);
    display: flex; align-items: center; justify-content: center; flex: none;
  }
  .contacts svg { width: 12px; height: 12px; fill: #fff; }
</style>
</head>
<body>

<section class="card card--back">
  <div class="back-photo" role="img" aria-label="Black and white street photograph of a person sleeping on a sidewalk beside a tree, with cars passing behind"></div>
  <div class="back-banner">
    <div class="org-name"><span class="org-dot"></span>Hearthway Housing</div>
    <div class="tagline">Opening Doors To Shelter</div>
  </div>
</section>

<section class="card card--front">
  <div class="front-logo">
    <span class="org-dot"></span>
    <span class="org-name">Hearthway Housing Center</span>
  </div>
  <div class="logo-rule"></div>

  <div class="rule rule--upper"></div>
  <div class="person">
    <div class="name">DANA ELLIS</div>
    <div class="title">Director</div>
  </div>

  <div class="address">1875 larkin avenue,<span>dallas tx 75201</span></div>

  <div class="rule rule--lower"></div>
  <ul class="contacts">
    <li>
      <span class="icon"><svg viewBox="0 0 24 24"><path d="M6.6 10.8a15 15 0 0 0 6.6 6.6l2.2-2.2c.3-.3.7-.4 1-.2 1.1.4 2.3.6 3.6.6.6 0 1 .4 1 1V20c0 .6-.4 1-1 1A17 17 0 0 1 3 4c0-.6.4-1 1-1h3.5c.6 0 1 .4 1 1 0 1.3.2 2.5.6 3.6.1.3 0 .7-.2 1z"/></svg></span>
      214 555 0187
    </li>
    <li>
      <span class="icon"><svg viewBox="0 0 24 24"><path d="M2 5h20v14H2zm2 2v.5l8 5 8-5V7zm0 2.8V17h16V9.8l-8 5z"/></svg></span>
      info@hearthwaydallas.org
    </li>
    <li>
      <span class="icon"><svg viewBox="0 0 24 24"><path d="M12 3 2 12h3v8h5v-5h4v5h5v-8h3z"/></svg></span>
      www.hearthwaydallas.org
    </li>
  </ul>
</section>

</body>
</html>
```